Ostrevan Capital LLC

Need Professional Business cards for New Investment Fund

Target Market(s)

High Quality investors

Industry/Entity Type

Financial

Contact Information for Business Card

Phone Number +1 555 284 6190
Name Lukas Varenko
Title Fund Manager
email lv@FundOstrevan.com
Website www.FundOstrevan.com

Colors

Designer to choose colors to be used in the design.

Requirements
Must have
• Must have our Logo and all of the above. Must be made so lettering and loge can be raised

```html
<!DOCTYPE html>
<html lang="en">
<head>
<meta charset="utf-8">
<title>Ostrevan Capital LLC – Business Card</title>
<link href="https://fonts.googleapis.com/css2?family=Roboto:wght@400;500&display=swap" rel="stylesheet">
<style>
  :root {
    --backdrop: #b4b4b4;
    --forest: #38423a;
    --forest-light: #5a665c;
    --lime: #8cc21f;
    --paper: #ffffff;
    --ink-light: #e9ece9;
  }
  html, body {
    margin: 0;
    width: 1200px;
    height: 1138px;
    overflow: hidden;
    background: var(--backdrop);
    font-family: "Roboto", Arial, sans-serif;
  }
  .card {
    position: absolute;
    width: 622px;
    height: 374px;
    border-radius: 18px;
    overflow: hidden;
  }
  .card-front {
    left: 274px;
    top: 186px;
    background: var(--forest);
  }
  .card-back {
    left: 276px;
    top: 608px;
    background: var(--paper);
  }
  .front-wordmark {
    position: absolute;
    left: 0;
    right: 0;
    top: 160px;
    text-align: center;
    font-size: 52px;
    font-weight: 500;
    letter-spacing: 2px;
    color: var(--forest-light);
    line-height: 1;
  }
  .back-lower {
    position: absolute;
    left: 0;
    right: 0;
    top: 190px;
    bottom: 0;
    background: var(--forest);
    border-top: 5px solid var(--lime);
  }
  .back-wordmark {
    position: absolute;
    left: 36px;
    top: 116px;
    display: flex;
    align-items: center;
    gap: 10px;
    font-size: 40px;
    font-weight: 500;
    letter-spacing: 1px;
    color: var(--forest);
    line-height: 1;
  }
  .back-wordmark .mark {
    width: 14px;
    height: 14px;
    background: var(--lime);
  }
  .holder {
    position: absolute;
    right: 30px;
    top: 210px;
    text-align: right;
    color: var(--ink-light);
  }
  .holder-name {
    font-size: 22px;
    font-weight: 500;
    margin: 0;
  }
  .holder-title {
    font-size: 15px;
    margin: 6px 0 0;
  }
  .contact-list {
    position: absolute;
    right: 30px;
    top: 285px;
    margin: 0;
    padding: 0;
    list-style: none;
    color: var(--ink-light);
    font-size: 15px;
    line-height: 23px;
  }
  .contact-list li {
    display: flex;
    justify-content: flex-end;
    align-items: center;
    gap: 7px;
  }
  .contact-list svg {
    width: 13px;
    height: 13px;
    fill: var(--ink-light);
  }
  .address {
    position: absolute;
    left: 36px;
    top: 308px;
    margin: 0;
    font-style: normal;
    color: var(--ink-light);
    font-size: 15px;
    line-height: 23px;
  }
</style>
</head>
<body>

<section class="card card-front" aria-label="Card front">
  <div class="front-wordmark">OSTREVAN</div>
</section>

<section class="card card-back" aria-label="Card back">
  <div class="back-wordmark"><span class="mark"></span>OSTREVAN</div>

  <div class="back-lower"></div>

  <div class="holder">
    <p class="holder-name">Lukas Varenko</p>
    <p class="holder-title">Fund Manager</p>
  </div>

  <ul class="contact-list">
    <li>+1 555 284 6190
      <svg viewBox="0 0 16 16"><path d="M2 5c0-2 2-3 6-3s6 1 6 3v1h-3V5H5v1H2zM4 7h8l2 7H2z"/></svg>
    </li>
    <li>lv@FundOstrevan.com
      <svg viewBox="0 0 16 16"><path d="M1 3h14v10H1zM2 4.5v.3l6 4 6-4v-.3z"/></svg>
    </li>
    <li>www.FundOstrevan.com
      <svg viewBox="0 0 16 16"><circle cx="8" cy="8" r="6.5" fill="none" stroke="#e9ece9" stroke-width="1.3"/><path d="M1.5 8h13M8 1.5v13" stroke="#e9ece9" stroke-width="1.1"/></svg>
    </li>
  </ul>

  <address class="address">
    14 Alder St.<br>
    Westbrook, NJ, 08990
  </address>
</section>

</body>
</html>
```